Modern Business Card For A Digital Advertising Company

I'll be print on the Pell Prints Velour paper http://us.pellprints.com/products/velour/business-cards.html
Need's to be modern and use the color palette of the logo or gray scales. I think integrating the pixelation of the logo in to the card and having it wrap from one side to the other could be interesting. My company provides ad operations, web development, and number of other services to websites around the world. You can see my website at http://www.zantorhq.com
Contact info on the card needs to have
Owen Lasko
President
p.318.204.6637
owen@zantorhq.com
http://www.zantorhq.com
Doesn't necessarily need to be in that order
Website owners
Business

```html
<!DOCTYPE html>
<html lang="en">
<head>
<meta charset="utf-8">
<title>Zantor HQ — Business Card</title>
<link rel="stylesheet" href="https://fonts.googleapis.com/css2?family=Source+Sans+3:wght@400;600;700&display=swap">
<style>
  :root {
    --stage: #2b2b2b;
    --paper: #ffffff;
    --green: #86bf40;
    --green-deep: #5a8a35;
    --charcoal: #333333;
    --ink: #3a3a3a;
    --rule: #b9b9b9;
  }
  * { box-sizing: border-box; margin: 0; padding: 0; }
  html, body {
    width: 1200px; height: 757px; overflow: hidden;
    background: var(--stage);
    font-family: "Source Sans 3", "Myriad Pro", Arial, sans-serif;
  }
  .card {
    position: absolute; top: 228px;
    width: 520px; height: 300px;
    overflow: hidden;
  }
  .card--front { left: 60px; background: var(--paper); }
  .card--back {
    left: 620px;
    background: linear-gradient(160deg, var(--green-deep) 0%, #6fa23b 50%, var(--green) 100%);
  }
  .front-wave { position: absolute; inset: 0; width: 100%; height: 100%; }
  .brand {
    position: absolute; left: 0; width: 222px; top: 98px;
    display: flex; align-items: center; justify-content: center; gap: 8px;
  }
  .brand__square { width: 18px; height: 18px; background: var(--green); flex: none; }
  .brand__name {
    font-size: 24px; font-weight: 700; color: var(--green);
    line-height: 1; white-space: nowrap;
  }
  .divider {
    position: absolute; left: 232px; top: 60px;
    width: 1px; height: 110px;
    background: linear-gradient(to bottom, transparent, var(--rule), transparent);
  }
  .contact { position: absolute; left: 248px; top: 62px; color: var(--ink); }
  .contact__name { font-size: 20px; font-weight: 700; color: var(--green); line-height: 1.1; }
  .contact__title { font-size: 13px; margin-top: 2px; }
  .contact__list { list-style: none; margin-top: 16px; font-size: 13px; }
  .contact__list li { display: flex; align-items: center; gap: 6px; line-height: 1.5; white-space: nowrap; }
  .contact__list svg { width: 11px; height: 11px; fill: var(--ink); flex: none; }
  .front-url {
    position: absolute; left: 0; right: 0; bottom: 18px;
    text-align: center; font-size: 14px; font-weight: 700;
    letter-spacing: 1.5px; color: var(--paper);
  }
  .back-brand {
    position: absolute; left: 0; right: 0; top: 92px;
    display: flex; align-items: center; justify-content: center; gap: 16px;
  }
  .back-brand__square { width: 44px; height: 44px; background: var(--paper); }
  .back-brand__name { font-size: 60px; font-weight: 700; color: var(--paper); line-height: 1; }
  .back-url {
    position: absolute; left: 0; right: 0; top: 200px;
    text-align: center; font-size: 18px; font-weight: 700;
    letter-spacing: 2px; color: var(--paper);
  }
</style>
</head>
<body>
  <section class="card card--front" aria-label="Business card front">
    <svg class="front-wave" viewBox="0 0 520 300" preserveAspectRatio="none" aria-hidden="true">
      <defs>
        <linearGradient id="wave-green" x1="0" y1="1" x2="1" y2="0">
          <stop offset="0" stop-color="#6fa23b"/>
          <stop offset="1" stop-color="#8cc443"/>
        </linearGradient>
      </defs>
      <path d="M0 262 C 140 250, 320 175, 520 150 L520 160 C 330 188, 150 262, 0 270 Z" fill="var(--charcoal)"/>
      <path d="M0 272 C 150 262, 330 192, 520 162 L520 300 L0 300 Z" fill="url(#wave-green)"/>
    </svg>

    <div class="brand">
      <span class="brand__square"></span>
      <span class="brand__name">Zantor HQ</span>
    </div>

    <div class="divider"></div>

    <div class="contact">
      <p class="contact__name">Owen Lasko</p>
      <p class="contact__title">President</p>
      <ul class="contact__list">
        <li>
          <svg viewBox="0 0 24 24" aria-hidden="true"><path d="M6.6 10.8a15.1 15.1 0 0 0 6.6 6.6l2.2-2.2c.3-.3.7-.4 1-.2 1.1.4 2.3.6 3.6.6.6 0 1 .4 1 1V20c0 .6-.4 1-1 1A17 17 0 0 1 3 4c0-.6.4-1 1-1h3.5c.6 0 1 .4 1 1 0 1.3.2 2.5.6 3.6.1.3 0 .7-.2 1z"/></svg>
          318.204.6637
        </li>
        <li>
          <svg viewBox="0 0 24 24" aria-hidden="true"><path d="M2 5h20v14H2zm2 2v.5l8 5 8-5V7l-8 5z"/></svg>
          owen@zantorhq.com
        </li>
      </ul>
    </div>

    <p class="front-url">www.zantorhq.com</p>
  </section>

  <section class="card card--back" aria-label="Business card back">
    <div class="back-brand">
      <span class="back-brand__square"></span>
      <span class="back-brand__name">Zantor HQ</span>
    </div>
    <p class="back-url">www.zantorhq.com</p>
  </section>
</body>
</html>
```